Web design for financial services

A modern web design of financial services (brokerage firm)
Req.s and technology tags :
- Very mobile friendly.
- One paged with some inner pages.
- Animated sticky header .
- Member login area for e-trade.
- Support RTL language.
- HTML & CSS.

The logo will be Home link
• MPTR :
WHO WE ARE
Content :
i) Board of Directors
ii) Mission Statement
iii) Corporate Values
iv) Regulations
• Financial Services :
WHAT WE DO
Content:
i) Electronic trading
ii) Trading desk
iii) Institutional
iv) Investors Education
• News
• Market Tools
• Forms---- opens new page
• Careers---- opens new page
• Contact Us----opens new page

The website is :
http://www.mptr-doha-example.com/

The logo need some changes to be more modern and impressively , but with keeping same structure .

Some related websites :
https://www.lv-bourse.example/

financial market

Financial Service

Coded - Design and coding required

2 page

• same fonts of http://www.kwdholdings.example/

• - Very mobile friendly.
• - One paged with some inner pages.
• - Animated sticky header .
• - Member login area for e-trade.
• - Support RTL language.
• - HTML & CSS.
• Slider , some Qatari theme,
• i like the video inside the home page
• ex :http://www.kwdholdings.example/

```html
<!DOCTYPE html>
<html lang="en">
<head>
<meta charset="utf-8">
<title>MPTR – Meridian Pearl Trading</title>
<link href="https://fonts.googleapis.com/css2?family=Lato:wght@300;400;700;900&display=swap" rel="stylesheet">
<style>
:root{
  --red:#a3191f;
  --red-dark:#8c1a1d;
  --ink:#2f2f2f;
  --muted:#7a7a7a;
  --light:#f3f3f3;
  --white:#ffffff;
  --card:#4a4a4a;
}
*{box-sizing:border-box;margin:0;padding:0}
html,body{width:1200px;height:2860px;overflow:hidden}
body{font-family:"Lato",Arial,sans-serif;color:var(--ink);background:var(--white)}
a{color:inherit;text-decoration:none}

/* Hero */
.hero{position:relative;height:700px;background:linear-gradient(180deg,#4c5866 0%,#6d7480 35%,#a99478 70%,#c9a26f 88%,#5e5a52 100%);color:var(--white)}
.site-header{position:absolute;top:0;left:0;right:0;height:120px;display:flex;align-items:center;padding:0 160px;background:linear-gradient(180deg,rgba(20,24,30,.55),rgba(20,24,30,0))}
.brand{display:flex;align-items:center;gap:14px;font-weight:900;font-size:34px;letter-spacing:1px}
.brand-dot{width:58px;height:58px;border-radius:50%;background:var(--red)}
.main-nav{display:flex;gap:34px;margin-left:110px;font-size:17px;font-weight:400}
.main-nav a.active{border-bottom:3px solid var(--red);padding-bottom:6px}
.header-tools{position:absolute;top:22px;right:140px;display:flex;gap:8px;font-size:13px}
.header-tools span{background:var(--red);padding:4px 12px}
.hero-play{position:absolute;left:560px;top:280px;width:80px;height:80px}
.hero-title{position:absolute;top:390px;left:0;right:0;text-align:center;font-size:46px;font-weight:700;line-height:1.12;letter-spacing:1px}

/* Who we are */
.who{display:flex;height:380px}
.who-text{width:620px;padding:60px 40px 0 160px}
.section-title{font-size:34px;font-weight:900;margin-bottom:22px}
.who-text p,.what-text p{font-size:14px;line-height:1.6;color:var(--muted);margin-bottom:14px}
.more{font-size:14px;font-weight:700;color:var(--red);border-bottom:2px solid var(--red)}
.who-photo{width:580px;height:380px;background:linear-gradient(135deg,#e9e9e9,#bfc4c8 55%,#8d949a)}

/* What we do */
.what{display:flex;height:440px;background:var(--light)}
.what-art{margin:60px 0 0 120px;width:440px;height:310px;background:radial-gradient(circle at 50% 50%,#c9464a 0,#d7d7d7 35%,var(--light) 70%)}
.what-text{width:500px;padding:90px 0 0 60px}
.what-text .section-title{color:var(--red)}

/* News */
.news{position:relative;height:360px;background:linear-gradient(180deg,#7a7a7a,#a8a8a8);padding:30px 150px 0}
.news .section-title{color:var(--white);font-weight:400;font-size:36px;margin-bottom:14px}
.news-list{display:flex;gap:20px}
.news-card{width:286px;background:var(--card);color:var(--white)}
.news-photo{height:130px;background:linear-gradient(135deg,#d8cdb8,#9a8a70 60%,#5c5446)}
.news-body{padding:12px 14px 14px}
.news-date{font-size:11px;color:#cfcfcf}
.news-title{font-size:20px;font-weight:700;margin:4px 0}
.news-body p{font-size:11px;line-height:1.45;color:#d6d6d6;margin-bottom:8px}
.news-body a{font-size:11px;font-weight:700;border-bottom:1px solid var(--white)}
.news-arrow{position:absolute;top:200px;width:24px;height:40px}
.news-arrow.prev{left:110px}.news-arrow.next{right:110px}

/* Market tools */
.tools{height:520px;padding:50px 150px 0}
.tools .section-title{font-weight:400;color:#555;font-size:34px}
.tools-list{display:flex;gap:26px}
.tool-box{width:282px;border:1px solid #d8d8d8;padding:16px 16px 24px;text-align:center}
.tool-box h3{font-size:16px;color:var(--red);font-weight:700;display:flex;align-items:center;gap:8px;justify-content:center}
.tool-box h3::before,.tool-box h3::after{content:"";flex:1;height:1px;background:var(--red)}
.tool-box ul{list-style:none;margin-top:14px}
.tool-box li{font-size:13px;color:var(--muted);padding:6px 0;border-bottom:1px solid #eee}

/* Footer */
.site-footer{height:460px;background:var(--red-dark);color:var(--white);position:relative;padding:60px 140px 0;display:flex}
.footer-brand{display:flex;align-items:center;gap:16px;font-weight:900;font-size:46px;width:330px;height:150px}
.footer-brand .brand-dot{width:80px;height:80px;background:var(--white)}
.footer-col{width:260px}
.footer-col h4{font-size:20px;font-weight:400;margin-bottom:14px}
.footer-col li{list-style:none;font-size:13px;line-height:1.9;color:#efd6d6}
.contact li{display:flex;align-items:center;gap:8px}
.contact svg{width:14px;height:14px;flex:none}
.social{display:flex;gap:8px}
.social span{width:30px;height:30px;border-radius:50%;background:var(--white)}
.copyright{position:absolute;bottom:28px;left:0;right:0;text-align:center;font-size:12px;color:#e4c3c3}
</style>
</head>
<body>

<section class="hero" role="img" aria-label="Photo of the Doha skyline at sunset">
  <header class="site-header">
    <a class="brand" href="#"><span class="brand-dot"></span>MPTR</a>
    <nav class="main-nav">
      <a class="active" href="#">MPTR</a>
      <a href="#">Financial Service</a>
      <a href="#">News</a>
      <a href="#">Market Tools</a>
      <a href="#">Forms</a>
      <a href="#">Careers</a>
    </nav>
    <div class="header-tools"><span>Login</span><span>English</span></div>
  </header>
  <svg class="hero-play" viewBox="0 0 80 80"><circle cx="40" cy="40" r="37" fill="none" stroke="#fff" stroke-width="3"/><path d="M32 26 L56 40 L32 54 Z" fill="#fff"/></svg>
  <h1 class="hero-title">WE ARE MERIDIAN PEARL<br>TRADING</h1>
</section>

<section class="who">
  <div class="who-text">
    <h2 class="section-title">WHO WE ARE</h2>
    <p>Meridian Pearl Trading is a private Qatari company that aims to provide secure and technologically advanced methods of trading to its clients. These facilities enable clients to trade faster, more securely and in private, keeping our strategy in mind with professional tools.</p>
    <p>Praesent elementum elit at tellus nisi ultrices mi amet porttitor mattis ante in massa libero interdum non interdum.</p>
    <a class="more" href="#">About MPTR &gt;</a>
  </div>
  <div class="who-photo" role="img" aria-label="Photo of business people reviewing financial documents"></div>
</section>

<section class="what">
  <div class="what-art" role="img" aria-label="Illustration of a briefcase surrounded by finance icons"></div>
  <div class="what-text">
    <h2 class="section-title">WHAT WE DO</h2>
    <p>Integer congue augue at malesuada dui elit amet nisi aliquet felis at cursus magna nisl nec elit. Posuere elementum elit at tellus nisi ultrices mi amet porttitor mattis ante in massa.</p>
    <p>Praesent elementum nisl at tellus nisi in ultrices amet porttitor mattis ante in massa libero interdum non.</p>
    <a class="more" href="#">Read More &gt;</a>
  </div>
</section>

<section class="news">
  <h2 class="section-title">News</h2>
  <svg class="news-arrow prev" viewBox="0 0 24 40"><path d="M18 4 L6 20 L18 36" fill="none" stroke="#fff" stroke-width="3"/></svg>
  <svg class="news-arrow next" viewBox="0 0 24 40"><path d="M6 4 L18 20 L6 36" fill="none" stroke="#fff" stroke-width="3"/></svg>
  <div class="news-list">
    <article class="news-card">
      <div class="news-photo" role="img" aria-label="Photo of a business meeting"></div>
      <div class="news-body"><div class="news-date">25 Jan 2016</div><h3 class="news-title">News Title here</h3><p>Praesent elementum elit at tellus nisi ultrices mi amet porttitor mattis ante in massa.</p><a href="#">READ MORE</a></div>
    </article>
    <article class="news-card">
      <div class="news-photo" role="img" aria-label="Photo of hands working at a laptop"></div>
      <div class="news-body"><div class="news-date">25 Jan 2016</div><h3 class="news-title">News Title here</h3><p>Praesent elementum elit at tellus nisi ultrices mi amet porttitor mattis ante in massa.</p><a href="#">READ MORE</a></div>
    </article>
    <article class="news-card">
      <div class="news-photo" role="img" aria-label="Photo of a desk with charts and papers"></div>
      <div class="news-body"><div class="news-date">25 Jan 2016</div><h3 class="news-title">News Title here</h3><p>Praesent elementum elit at tellus nisi ultrices mi amet porttitor mattis ante in massa.</p><a href="#">READ MORE</a></div>
    </article>
  </div>
</section>

<section class="tools">
  <h2 class="section-title">Market Tools</h2>
  <div class="tools-list">
    <div class="tool-box"><h3>Most Active Company</h3><ul>
      <li>Praesent elementum</li><li>Elit at tellus</li><li>Ultrices mi</li><li>Amet porttitor</li><li>Mattis ante in</li><li>Massa libero</li><li>Interdum non</li><li>Nisi interdum</li></ul></div>
    <div class="tool-box"><h3>Top Gainer</h3><ul>
      <li>Donec dictum</li><li>Luctus nisl odio</li><li>Cras a ante vitae</li><li>Nunc lobortis aliquam</li><li>Mauris nunc ipsum</li><li>Venenatis nisi</li><li>Euismod sit amet</li></ul></div>
    <div class="tool-box"><h3>Top Losers</h3><ul>
      <li>Libero interdum</li><li>Praesent elementum</li><li>Elit at tellus</li><li>Ultrices mi</li><li>Amet porttitor</li><li>Mattis ante in</li><li>Massa libero</li></ul></div>
  </div>
</section>

<footer class="site-footer">
  <div class="footer-brand"><span class="brand-dot"></span>MPTR</div>
  <div class="footer-col"><h4>Company</h4><ul>
    <li>MPTR</li><li>Financial Service</li><li>News</li><li>Market Tool</li><li>Forms</li><li>Careers</li></ul></div>
  <div class="footer-col contact"><h4>Contact Us</h4><ul>
    <li><svg viewBox="0 0 14 14"><path d="M7 1a4 4 0 0 0-4 4c0 3 4 8 4 8s4-5 4-8a4 4 0 0 0-4-4z" fill="#fff"/></svg>4th floor, Corniche Tower, Suite 700</li>
    <li><svg viewBox="0 0 14 14"></svg>Doha, Qatar 00000</li>
    <li><svg viewBox="0 0 14 14"><path d="M3 1l3 3-2 2c1 2 2 3 4 4l2-2 3 3-2 2C6 13 1 8 1 3z" fill="#fff"/></svg>+974 0000 0000</li>
    <li><svg viewBox="0 0 14 14"><rect x="1" y="3" width="12" height="8" fill="none" stroke="#fff"/><path d="M1 3l6 5 6-5" fill="none" stroke="#fff"/></svg>info@mptr-example.com</li></ul></div>
  <div class="footer-col"><h4>Follow Us</h4>
    <div class="social"><span></span><span></span><span></span><span></span><span></span></div></div>
  <p class="copyright">© 2017 Company Name. All rights reserved.</p>
</footer>

</body>
</html>
```